High impact classy folder for an HVAC and Electrical contractor

We need a folder designed. It needs to be high impact and classy with a rich look to it. We want to cement our branding via the use of the folder so the look will need to have impact with use of our logo and colors.

We want to pull the entire brand look and feel together with this folder. We are going to be making other marketing materials and this is the start of a much larger project. In the ideal situation the winning desginer will continue on with the rest of the projects because they will know how to apply the brand look.

We want to give our local company the feel of a national franchise. Wherein the brand is very prominent and is repeated over and over again.

Use of logo and color scheme will be important.

We like dark backgrounds because they really make the logo pop.

Target Market(s)

homeowners

Font styles to use
Serif

Requirements
Must have
• Logo prominent on the front
• Our Tag Line:
• The Best Way To Live In New Jersey Is With Harbel"
• On the inside pockets:
• Our Phone number: 973-555-0148
• A message to our customers:
• We want to thank you for choosing Harbel Tradeworks today
• Our name says it all, because for over 30 years we have prided ourselves on delivering the best service and exceeding our customers' expectations everyday. Whether you need something fixed, replaced or upgraded, no matter how large or small, the dedicated and experts at Harbel Tradeworks are here to take care of you. Delivering the right solution for you the first time- everytime - and ensuring you are always 100% satisfied. If for any reason you want to speak with us, please do not hesitate to call or email. Thank you again for choosing Harbel Tradeworks.
• On the rear: a graphic that says 24-7 service
• A list of other services we provide:
• Solar
• Generators
• Home Security
• Home Automation
• Home Inspection
• Energy Audits
• 1 Day Bathroom remodles
• Basement Waterproofing
• Garage Doors
• Home Theaters
Nice to have
• I added photos of a flyer and of a mobile website to give an idea of the color scheme as well

```html
<!DOCTYPE html>
<html lang="en">
<head>
<meta charset="utf-8">
<title>Harbel Tradeworks — Presentation Folder</title>
<link href="https://fonts.googleapis.com/css2?family=Playfair+Display:wght@700&family=Raleway:ital,wght@0,400;0,500;0,600;0,700;1,400&display=swap" rel="stylesheet">
<style>
  :root {
    --red: #9b1b2a;
    --red-deep: #7a1320;
    --cream: #efe9dc;
    --pocket-cream: #f7f0c9;
    --gold: #f1d79a;
    --orange: #e8893a;
    --navy: #2f3a5c;
    --backdrop: #b9b9bb;
  }
  * { box-sizing: border-box; margin: 0; padding: 0; }
  html, body { width: 842px; height: 1200px; overflow: hidden; }
  body { background: var(--backdrop); font-family: "Raleway", sans-serif; position: relative; }

  .spread { position: absolute; left: 21px; width: 800px; height: 560px; display: flex; box-shadow: 0 8px 22px rgba(0,0,0,.22); }
  .spread--outside { top: 20px; }
  .spread--inside { top: 620px; }
  .panel { position: relative; width: 400px; height: 560px; overflow: hidden; }

  /* Back cover */
  .back { background: linear-gradient(160deg, var(--red) 0%, var(--red-deep) 100%); color: var(--cream); text-align: center; }
  .back__frame { position: absolute; inset: 12px; border: 1.5px solid var(--gold); }
  .brand-name { font-family: "Playfair Display", serif; font-weight: 700; color: var(--gold); line-height: 1.02; }
  .back .brand-name { margin-top: 70px; font-size: 50px; }
  .back__heading { margin-top: 40px; font-weight: 700; font-size: 15px; letter-spacing: 1px; }
  .services { margin-top: 12px; font-size: 13px; line-height: 1.55; }
  .service-badge { margin: 34px auto 0; display: flex; align-items: center; justify-content: center; gap: 10px; color: var(--gold); }
  .service-badge__text { font-size: 30px; font-style: italic; font-weight: 400; }
  .service-badge__text small { font-size: 22px; }
  .web-bar { margin: 24px auto 0; width: 230px; background: var(--orange); color: var(--red-deep); font-weight: 700; font-size: 11.5px; padding: 6px 0; clip-path: polygon(4% 0, 100% 0, 96% 100%, 0 100%); }
  .address { margin-top: 14px; font-size: 14px; font-weight: 600; color: var(--gold); }
  .licenses { margin-top: 5px; font-size: 9.5px; line-height: 1.45; color: var(--gold); }

  /* Front cover */
  .front { background: var(--cream); }
  .front__band { position: absolute; top: 0; left: 0; width: 400px; height: 150px; }
  .front__brand { position: absolute; top: 26px; left: 0; width: 400px; text-align: center; }
  .front__brand .brand-name { font-size: 40px; }
  .front__brand span { display: block; margin-top: 6px; font-size: 10px; font-weight: 700; letter-spacing: 3px; color: var(--orange); }
  .front__photo { position: absolute; top: 156px; left: 24px; width: 352px; height: 280px; border-radius: 6px;
    background: radial-gradient(ellipse at 50% 65%, #3a2a2c 0%, #8d7c78 35%, #d9d2c6 70%, var(--cream) 100%); }
  .tagline { position: absolute; top: 466px; width: 400px; text-align: center; font-size: 19px; font-weight: 600; line-height: 1.3; color: var(--navy); }
  .tagline em { font-style: normal; font-weight: 700; color: var(--red); }

  /* Inside */
  .inside { background: var(--pocket-cream); }
  .inside + .inside { border-left: 1px solid #e3d9a8; }
  .watermark { position: absolute; top: 110px; width: 400px; text-align: center; font-family: "Playfair Display", serif; font-weight: 700; font-size: 46px; line-height: 1.05; color: #ebe0b0; }
  .pocket { position: absolute; left: 0; bottom: 0; width: 400px; height: 210px; background: linear-gradient(160deg, var(--red) 0%, var(--red-deep) 100%); color: var(--cream); box-shadow: 0 -3px 8px rgba(0,0,0,.15); }
  .pocket--left { clip-path: polygon(0 0, 100% 18%, 100% 100%, 0 100%); }
  .pocket--right { clip-path: polygon(0 18%, 100% 0, 100% 100%, 0 100%); }
  .pocket__message { position: absolute; left: 28px; right: 28px; top: 50px; font-size: 9.6px; line-height: 1.5; text-align: justify; }
  .pocket__thanks { position: absolute; top: 64px; width: 400px; text-align: center; font-size: 14px; font-style: italic; line-height: 1.5; }
  .pocket__thanks strong { font-style: normal; font-weight: 700; }
  .phone { position: absolute; top: 128px; width: 400px; display: flex; align-items: center; justify-content: center; gap: 12px; font-size: 28px; font-weight: 700; letter-spacing: 1px; color: #fff; }
  .phone__rule { width: 36px; height: 6px; border-top: 1.5px solid var(--cream); border-bottom: 1.5px solid var(--cream); }
</style>
</head>
<body>

<section class="spread spread--outside" aria-label="Folder outside">
  <div class="panel back">
    <div class="back__frame"></div>
    <div class="brand-name">Harbel<br>Tradeworks</div>
    <p class="back__heading">WE PROVIDE</p>
    <p class="services">
      Solar • Generators • Home Security<br>
      Home Automation • Home Inspection • Energy Audits<br>
      1 Day Bathroom remodles • Basement Waterproofing<br>
      Garage Doors • Home Theaters
    </p>
    <div class="service-badge">
      <svg width="44" height="44" viewBox="0 0 44 44" fill="none" stroke="currentColor" stroke-width="2.2" stroke-linecap="round">
        <path d="M36 12 A17 17 0 1 0 39 24"/>
        <path d="M33 8 L36.5 12.5 L31 13.5"/>
        <path d="M22 12 V22 L29 27"/>
      </svg>
      <span class="service-badge__text">24/7 <small>Service</small></span>
    </div>
    <div class="web-bar">www.HarbelTradeworks.com</div>
    <p class="address">P.O. Box 418, Fernbrook, NJ 07990</p>
    <p class="licenses">
      NJ HVAC License # 204 | NJ Electrical License # 30519<br>
      NJ Home Improvement Business Registration # 13VH08812400
    </p>
  </div>

  <div class="panel front">
    <svg class="front__band" viewBox="0 0 400 150" preserveAspectRatio="none" aria-hidden="true">
      <path d="M0 0 H400 V128 C330 128 320 118 200 118 C80 118 70 128 0 128 Z" fill="var(--red)"/>
    </svg>
    <div class="front__brand">
      <div class="brand-name">Harbel<br>Tradeworks</div>
      <span>HOME SERVICES</span>
    </div>
    <div class="front__photo" role="img" aria-label="Photo of a smiling family behind the company service van in red and black livery"></div>
    <p class="tagline">The Best Way To Live In<br>New Jersey Is With <em>Harbel!</em></p>
  </div>
</section>

<section class="spread spread--inside" aria-label="Folder inside pockets">
  <div class="panel inside">
    <div class="watermark" aria-hidden="true">Harbel<br>Tradeworks</div>
    <div class="pocket pocket--left">
      <p class="pocket__message">Our name says it all, because for over 30 years we have prided ourselves on delivering the best service and exceeding our customers' expectations everyday. Whether you need something fixed, replaced or upgraded, no matter how large or small, the dedicated and experts at Harbel Tradeworks are here to take care of you. Delivering the right solution for you the first time- everytime - and ensuring you are always 100% satisfied. If for any reason you want to speak with us, please do not hesitate to call or email. Thank you again for choosing Harbel Tradeworks.</p>
    </div>
  </div>
  <div class="panel inside">
    <div class="watermark" aria-hidden="true">Harbel<br>Tradeworks</div>
    <div class="pocket pocket--right">
      <p class="pocket__thanks">We want to thank you for choosing<br><strong>Harbel Tradeworks today</strong></p>
      <div class="phone"><span class="phone__rule"></span>973-555-0148<span class="phone__rule"></span></div>
    </div>
  </div>
</section>

</body>
</html>
```